Halberd Guard Services

Our Company is a security business which needs a cut edge design, the final product should have all relevant information and maintain a bold but modern and professional look.

Target Market(s)

A cut edge design which will attract any audience

Industry/Entity Type

Security

Contact Information for Business Card

HALBERD GUARD SERVICES

Gregor Lindqvist
Operations Manager
Phone: 0491 735 219

Email: info@halberdguard.com.au
Web: www.halberdguard.com.au

Requirements
Must have
• Must be double sided and contain all relevant information and the company logo.

```html
<!DOCTYPE html>
<html lang="en">
<head>
<meta charset="utf-8">
<title>Halberd Guard Services – Business Card</title>
<link href="https://fonts.googleapis.com/css2?family=Open+Sans:wght@400;600;800&display=swap" rel="stylesheet">
<style>
  :root {
    --bg: #e6e8e9;
    --card-white: #ffffff;
    --teal: #4d6f77;
    --orange: #f5a21a;
    --slate: #37474f;
    --grey-text: #5c666b;
    --light: #ffffff;
  }
  * { box-sizing: border-box; margin: 0; padding: 0; }
  html, body {
    width: 1200px; height: 951px; overflow: hidden;
    background: var(--bg);
    font-family: "Open Sans", Arial, sans-serif;
  }
  .stage {
    width: 1200px; height: 951px;
    display: flex; flex-direction: column; align-items: center; justify-content: center;
    gap: 50px;
  }
  .card {
    width: 700px; height: 400px;
    border-radius: 22px; overflow: hidden;
    background: var(--card-white);
    box-shadow: 0 6px 18px rgba(0,0,0,0.18);
    position: relative;
  }

  /* Front */
  .card-front { display: flex; }
  .card-front .edge { width: 22px; background: var(--teal); }
  .card-front .face {
    flex: 1; display: flex; flex-direction: column; align-items: center; justify-content: center;
    gap: 42px;
  }
  .brand { display: flex; align-items: center; gap: 16px; }
  .brand-dot { border-radius: 50%; background: var(--teal); flex: none; }
  .brand-name { font-weight: 800; color: var(--slate); letter-spacing: 0.5px; white-space: nowrap; }
  .brand-lg .brand-dot { width: 56px; height: 56px; }
  .brand-lg .brand-name { font-size: 34px; }
  .website { font-size: 20px; color: var(--grey-text); letter-spacing: 2px; }

  /* Back */
  .card-back { display: flex; flex-direction: column; }
  .card-back .top {
    height: 188px; display: flex; align-items: center; justify-content: center;
    background: linear-gradient(#ffffff, #f3f4f4);
  }
  .brand-sm .brand-dot { width: 36px; height: 36px; }
  .brand-sm .brand-name { font-size: 24px; }
  .card-back .rule { height: 7px; background: var(--orange); }
  .card-back .details {
    flex: 1; background: var(--teal); color: var(--light);
    padding: 26px 40px 0 48px;
    display: flex; flex-direction: column; align-items: flex-end;
  }
  .person { font-size: 30px; font-weight: 400; color: var(--orange); margin-right: 150px; }
  .contact { font-size: 19px; font-weight: 600; line-height: 1.45; }
  .phone { margin-right: 170px; margin-top: 6px; }
  .online { display: flex; gap: 40px; }
  .address { white-space: nowrap; }
</style>
</head>
<body>
<main class="stage">
  <section class="card card-front" aria-label="Business card front">
    <div class="edge"></div>
    <div class="face">
      <div class="brand brand-lg">
        <span class="brand-dot"></span>
        <span class="brand-name">HALBERD GUARD SERVICES</span>
      </div>
      <p class="website">www.halberdguard.com.au</p>
    </div>
  </section>

  <section class="card card-back" aria-label="Business card back">
    <div class="top">
      <div class="brand brand-sm">
        <span class="brand-dot"></span>
        <span class="brand-name">HALBERD GUARD SERVICES</span>
      </div>
    </div>
    <div class="rule"></div>
    <div class="details">
      <p class="person">Gregor Lindqvist</p>
      <p class="contact phone">Phone: 0491 735 219</p>
      <p class="contact online"><span>info@halberdguard.com.au</span><span>www.halberdguard.com.au</span></p>
      <p class="contact address">4100 Vale Ridge Rd., Suite 210-118, Corvin, TX 78014</p>
    </div>
  </section>
</main>
</body>
</html>
```